PulseClaimDesk.Com PowerPoint

I need a PowerPoint layout for my presentations. My business is called PulseClaimDesk.Com - my presentations teach cardiologists how to document their procedures and visits and teaches them how to bill accurately for them.

Industry/Entity Type

Business

Requirements
Must have
• the logo should be subtly there on each page - perhaps as a watermark? I'm really not creative; please help.

```html
<!DOCTYPE html>
<html lang="en">
<head>
<meta charset="utf-8">
<title>PulseClaimDesk.Com – Presentation Template</title>
<link rel="stylesheet" href="https://fonts.googleapis.com/css2?family=Graduate&family=Cinzel:wght@500&family=Open+Sans:wght@400;600&display=swap">
<style>
  :root {
    --red: #c0202e;
    --dark-red: #8c1a22;
    --bar: #1f1f1f;
    --ink: #111;
    --paper-light: #eeeeee;
    --paper-mid: #dadada;
    --paper-edge: #c9c9c9;
    --white: #fff;
    --muted: #cfcfcf;
  }
  * { box-sizing: border-box; margin: 0; padding: 0; }
  html, body { width: 1200px; height: 900px; overflow: hidden; background: var(--white); }
  body { position: relative; font-family: "Open Sans", Arial, sans-serif; }

  .slide {
    position: absolute; width: 570px; height: 320px; overflow: hidden;
    background: radial-gradient(ellipse at 45% 40%, var(--paper-light) 0%, var(--paper-mid) 70%, var(--paper-edge) 100%);
  }
  .slide--bullets { left: 22px; top: 166px; }
  .slide--image   { left: 604px; top: 166px; }
  .slide--title   { left: 22px; top: 494px; }
  .slide--closing { left: 605px; top: 494px; }

  .corner { position: absolute; width: 58px; height: 52px; }
  .corner--top { right: 8px; top: 6px; }
  .corner--bottom { right: 10px; bottom: 8px; }
  .corner-number {
    position: absolute; color: var(--white); font-family: "Graduate", serif; font-size: 13px;
  }
  .corner--top .corner-number { right: 5px; top: 9px; }
  .corner--bottom .corner-number { right: 6px; bottom: 6px; font-size: 18px; }

  .rule-line { position: absolute; left: 8px; top: 11px; width: 540px; height: 24px; }

  .main-bullet {
    position: absolute; left: 53px; top: 46px; display: flex; align-items: center; gap: 8px;
    font-family: "Graduate", serif; font-size: 21px; color: var(--red);
  }
  .sub-bullets { position: absolute; left: 97px; top: 78px; list-style: none; }
  .sub-bullets li {
    display: flex; align-items: center; gap: 5px; height: 28px;
    font-family: "Cinzel", serif; font-size: 11.5px; color: #222;
  }

  .title-bar {
    position: absolute; left: 8px; top: 244px; width: 553px; height: 70px; background: var(--bar);
  }
  .title-bar h2 {
    position: absolute; left: 10px; top: 4px; font-family: "Graduate", serif; font-weight: 400;
    font-size: 35px; color: var(--red); letter-spacing: 0.5px;
  }
  .title-bar .underline {
    position: absolute; left: 10px; top: 45px; width: 210px; height: 2px; background: var(--white);
  }
  .title-bar .caption {
    position: absolute; top: 50px; font-size: 9px; color: var(--white);
  }
  .brand-mark {
    position: absolute; right: 10px; bottom: 8px; display: flex; align-items: center; gap: 4px;
    font-size: 8px; font-weight: 600; color: var(--muted);
  }
  .brand-mark .dot { width: 8px; height: 8px; background: var(--red); }

  .image-frame { position: absolute; left: 13px; top: 17px; width: 238px; height: 210px; background: var(--bar); }
  .image-mat { position: absolute; left: 5px; top: 6px; width: 200px; height: 199px; background: var(--red); }
  .image-area {
    position: absolute; left: 20px; top: 37px; width: 160px; height: 136px;
    background: linear-gradient(135deg, #f3f3f3, #d9d9d9);
  }
  .image-label {
    position: absolute; left: 205px; top: 0; width: 33px; height: 210px;
    writing-mode: vertical-rl; transform: rotate(180deg);
    display: flex; align-items: center; justify-content: center;
    color: var(--white); font-size: 11px;
  }

  .page-title { position: absolute; left: 0; width: 570px; text-align: center; }
  .page-title h1 {
    font-family: "Graduate", serif; font-weight: 400; font-size: 52px; color: var(--red);
    line-height: 1; padding-left: 10px; margin-top: 26px;
  }
  .page-title .details { font-size: 11.5px; color: var(--ink); font-weight: 600; margin-left: 10px; }
  .reflection {
    transform: scaleY(-1); opacity: 0.35;
    -webkit-mask-image: linear-gradient(to top, #000 0%, transparent 70%);
    mask-image: linear-gradient(to top, #000 0%, transparent 70%);
  }
  .page-title .reflection h1 { margin-top: 0; }

  .emblem {
    position: absolute; left: 233px; top: 150px; width: 124px; height: 124px; border-radius: 50%;
    background: var(--red); display: flex; align-items: center; justify-content: center;
    font-size: 11px; font-weight: 600; color: var(--white);
  }
  .site-url { position: absolute; left: 0; top: 290px; width: 580px; text-align: center; font-size: 12px; color: #222; }

  .closing { position: absolute; left: 0; top: 128px; width: 570px; text-align: center; }
  .closing h1 {
    font-family: "Graduate", serif; font-weight: 400; font-size: 56px; color: var(--red); line-height: 1;
  }
  .closing .reflection h1 { color: #6f86b8; }
</style>
</head>
<body>

<section class="slide slide--bullets">
  <svg class="rule-line" viewBox="0 0 540 24">
    <polygon points="11,2 19,5 21,12 19,19 11,22 3,19 1,12 3,5" fill="none" stroke="#333" stroke-width="1.5"/>
    <circle cx="11" cy="12" r="5" fill="var(--red)"/>
    <line x1="22" y1="12" x2="540" y2="12" stroke="#333" stroke-width="2"/>
  </svg>
  <svg class="corner corner--top" viewBox="0 0 58 52"><polygon points="0,0 58,0 58,52" fill="var(--red)"/></svg>
  <div class="corner corner--top"><span class="corner-number">03</span></div>

  <div class="main-bullet">
    <svg width="20" height="20" viewBox="0 0 20 20"><polygon points="10,1 17,4 19,11 15,18 5,18 1,11 3,4" fill="none" stroke="var(--red)" stroke-width="3"/></svg>
    <span>MAIN BULLET</span>
  </div>
  <ul class="sub-bullets">
    <li><svg width="16" height="16" viewBox="0 0 16 16"><polygon points="5,1 11,1 15,5 15,11 11,15 5,15 1,11 1,5" fill="var(--red)" stroke="#222" stroke-width="2"/></svg>SUB BULLET FORM</li>
    <li><svg width="16" height="16" viewBox="0 0 16 16"><polygon points="5,1 11,1 15,5 15,11 11,15 5,15 1,11 1,5" fill="var(--red)" stroke="#222" stroke-width="2"/></svg>SUB BULLET FORM</li>
    <li><svg width="16" height="16" viewBox="0 0 16 16"><polygon points="5,1 11,1 15,5 15,11 11,15 5,15 1,11 1,5" fill="var(--red)" stroke="#222" stroke-width="2"/></svg>SUB BULLET FORM</li>
  </ul>

  <div class="title-bar">
    <h2>SLIDE TITLE</h2>
    <div class="underline"></div>
    <span class="caption" style="left:158px">BULLET FORM</span>
    <div class="brand-mark"><span class="dot"></span>PulseClaimDesk.Com</div>
  </div>
</section>

<section class="slide slide--image">
  <svg class="corner corner--top" viewBox="0 0 58 52"><polygon points="0,0 58,0 58,52" fill="var(--red)"/></svg>
  <div class="corner corner--top"><span class="corner-number">02</span></div>

  <div class="image-frame">
    <div class="image-mat">
      <div class="image-area" role="img" aria-label="Slide image placeholder"></div>
    </div>
    <div class="image-label">sample image placement</div>
  </div>

  <div class="title-bar">
    <h2>SLIDE TITLE</h2>
    <div class="underline"></div>
    <span class="caption" style="left:38px">DETAILS OF SLIDE / NAME OF PRESENTOR</span>
    <div class="brand-mark"><span class="dot"></span>PulseClaimDesk.Com</div>
  </div>
</section>

<section class="slide slide--title">
  <div class="page-title">
    <h1>TITLE PAGE</h1>
    <p class="details">DETAILS OF PRESENTATION / NAME OF PRESENTOR</p>
    <div class="reflection">
      <h1>TITLE PAGE</h1>
      <p class="details">DETAILS OF PRESENTATION / NAME OF PRESENTOR</p>
    </div>
  </div>
  <div class="emblem">PulseClaimDesk.Com</div>
  <p class="site-url">http://www.pulseclaimdesk.com/</p>
  <svg class="corner corner--bottom" viewBox="0 0 58 52"><polygon points="58,0 58,52 0,52" fill="var(--red)"/></svg>
  <div class="corner corner--bottom"><span class="corner-number">01</span></div>
</section>

<section class="slide slide--closing">
  <div class="closing">
    <h1>THANK YOU</h1>
    <div class="reflection"><h1>THANK YOU</h1></div>
  </div>
  <svg class="corner corner--bottom" viewBox="0 0 58 52"><polygon points="58,0 58,52 0,52" fill="var(--red)"/></svg>
  <div class="corner corner--bottom"><span class="corner-number">X</span></div>
</section>

</body>
</html>
```